Post Card Design - Photo on front, details on back. Logo on both sides.

Back: See the photo of my old card. The back worked well, as it gave me lots of space to write on. The address details are still correct, but the logo has changed to Josephine Sans. Logo can be on one line or on two (if two, align it on the left).
Don't include the 'BEAUTIFUL WEDDING DRESSES...' bit.
I'd like to print this on thicker, slightly coarse paper, so don't go too small on detail.
Here are the Trelo paper details: Paper Stock: Natural Uncoated
Paper Thickness: Premium
Finish: None
Front of Card: I'd like to see options for both pictures:
I think the painted image would look best with a frame in a pale shade and the logo in the frame fairly subtle.
The actual dress photo I'd like to see cropped a bit like in my mock up. You'll need to have a look at how the logo would be best placed on this. You can place it anywhere, or add a banner.
See my website for my brand's look: mirelhoffkin.co.nz
Target Market(s)
Brides
Industry/Entity Type
Wedding Dresses
Contact Information for Business Card
Front: Photo and logo. Back: with details and lots of empty space. See attached photos for loose brief.
Other font styles liked:
- Josephine Sans
Requirements
Must have
- I hand-write the gown designs and price on the back of the card, so there needs to be plenty of empty space.
Nice to have
- As per brief.
Should not have
- It must look clean, romantic, modern. Timeless.

```html
<!DOCTYPE html>
<html lang="en">
<head>
<meta charset="utf-8">
<title>Mirel Hoffkin – Post Card</title>
<link rel="stylesheet" href="https://fonts.googleapis.com/css2?family=Josefin+Sans:wght@300;400&family=Open+Sans:wght@400&display=swap">
<style>
  :root {
    --backdrop: #ebebec;
    --card-edge: #d4d4d6;
    --front-cream: #f3e5bd;
    --front-cream-deep: #ecd9a8;
    --ink: #1e1e20;
    --back-white: #f7f7f7;
    --band-grey: #b9babd;
    --band-ink: #3d3e42;
    --art-rose: #eaa6ad;
    --art-blush: #f2c8c4;
    --art-peach: #f0c9a4;
  }
  * { margin: 0; padding: 0; box-sizing: border-box; }
  html, body { width: 1200px; height: 900px; overflow: hidden; }
  body { background: var(--backdrop); position: relative; font-family: "Josefin Sans", sans-serif; }

  .card { position: absolute; box-shadow: 0 0 0 1px var(--card-edge); overflow: hidden; }

  /* Front */
  .card-front {
    left: 100px; top: 58px; width: 555px; height: 367px;
    background: radial-gradient(ellipse at 70% 50%, var(--front-cream) 40%, var(--front-cream-deep) 100%);
  }
  .front-logo {
    position: absolute; top: 36px;
    writing-mode: vertical-rl;
    font-family: "Josefin Sans", sans-serif; font-weight: 300;
    color: var(--ink); line-height: 1; white-space: nowrap;
  }
  .front-logo--first { left: 97px; font-size: 84px; letter-spacing: 3px; }
  .front-logo--last { left: 34px; font-size: 43px; letter-spacing: 2px; }
  .front-artwork {
    position: absolute; left: 188px; top: 38px; width: 330px; height: 300px;
    border-radius: 46% 42% 44% 48%;
    background:
      radial-gradient(circle at 30% 35%, var(--art-rose) 0%, transparent 45%),
      radial-gradient(circle at 60% 70%, var(--art-peach) 0%, transparent 45%),
      radial-gradient(circle at 50% 50%, var(--art-blush) 0%, var(--front-cream) 78%);
  }

  /* Back */
  .card-back {
    left: 546px; top: 474px; width: 554px; height: 368px;
    background: var(--back-white);
  }
  .back-logo {
    position: absolute; left: 52px; top: 52px;
    font-family: "Josefin Sans", sans-serif; font-weight: 400;
    font-size: 24px; letter-spacing: 1.6px; color: var(--ink);
  }
  .contact-band {
    position: absolute; left: 0; bottom: 0; width: 100%; height: 57px;
    background: var(--band-grey);
    display: flex; align-items: center; gap: 14px; padding-left: 52px;
    font-family: "Open Sans", sans-serif; font-size: 13px; color: var(--band-ink);
  }
  .contact-item { display: flex; align-items: center; gap: 3px; white-space: nowrap; }
  .contact-icon { width: 11px; height: 11px; fill: none; stroke: var(--band-ink); stroke-width: 1.4; }
</style>
</head>
<body>

  <section class="card card-front" aria-label="Post card front">
    <span class="front-logo front-logo--first">MIREL</span>
    <span class="front-logo front-logo--last">HOFFKIN</span>
    <div class="front-artwork" role="img" aria-label="Painted illustration of a bridal couple embracing among pink and peach peony flowers"></div>
  </section>

  <section class="card card-back" aria-label="Post card back">
    <h1 class="back-logo">MIREL HOFFKIN</h1>
    <footer class="contact-band">
      <span class="contact-item">
        <svg class="contact-icon" viewBox="0 0 12 12" aria-hidden="true"><path d="M3 1 L5 3.5 L4 5 Q5.5 7.5 7 8 L8.5 7 L11 9 L9.5 11 Q4 10.5 1 3 Z"/></svg>
        +64 9 555 0142
      </span>
      <span class="contact-item">
        <svg class="contact-icon" viewBox="0 0 12 12" aria-hidden="true"><circle cx="6" cy="6" r="5"/><ellipse cx="6" cy="6" rx="2.2" ry="5"/><path d="M1 6 H11"/></svg>
        mirelhoffkin.co.nz
      </span>
      <span class="contact-item">
        <svg class="contact-icon" viewBox="0 0 12 12" aria-hidden="true"><rect x="1" y="2.5" width="10" height="7"/><path d="M1 2.5 L6 6.5 L11 2.5"/></svg>
        mirel@mirelhoffkin.co.nz
      </span>
    </footer>
  </section>

</body>
</html>
```